Business Card Design for Occupational Medicine Start Up Company

We need to design a professional business card. We are a healthcare company providing occupational medicine services to blue collar industries. We are professional, efficient and high quality service providers.

Target Market(s)

Blue Collar Industry: Shipbuilding, Ports, Trucking Companies; The Executives and Safety Officers for these companies

Industry/Entity Type

Healthcare

Contact Information for Business Card

Logo, Name, Title, Email, Phone

Other font styles liked:
• Please match our Brand Guide

Requirements
Must have
• Our Company Colors and Logo

```html
<!DOCTYPE html>
<html lang="en">
<head>
<meta charset="utf-8">
<title>CrewWell Clinics — Business Card</title>
<link href="https://fonts.googleapis.com/css2?family=Montserrat:wght@400;500;700;800&display=swap" rel="stylesheet">
<style>
  :root {
    --navy: #2c2a72;
    --navy-deep: #232161;
    --sky: #2ea3dc;
    --amber: #f5b335;
    --paper: #ffffff;
    --ink: #2c2a72;
    --text: #2a2a3a;
    --backdrop: #3a3a3c;
  }
  * { box-sizing: border-box; margin: 0; padding: 0; }
  html, body {
    width: 1200px; height: 1186px; overflow: hidden;
    background: var(--backdrop);
    font-family: "Montserrat", Arial, sans-serif;
  }
  .sheet {
    width: 1200px; height: 1186px;
    display: flex; flex-direction: column; align-items: center; justify-content: center;
    gap: 50px;
  }
  .card {
    width: 880px; height: 503px; border-radius: 28px;
    position: relative; overflow: hidden;
  }
  /* front */
  .card-front { background: var(--navy); display: flex; align-items: center; justify-content: center; }
  .brand { display: flex; align-items: center; gap: 22px; }
  .brand-dot { width: 64px; height: 64px; border-radius: 50%; flex: none; }
  .card-front .brand-dot { background: var(--amber); }
  .brand-name { font-weight: 800; letter-spacing: 1px; text-transform: uppercase; white-space: nowrap; }
  .card-front .brand-name { color: var(--paper); font-size: 54px; }

  /* back */
  .card-back { background: var(--paper); }
  .card-back .brand { position: absolute; left: 60px; top: 70px; gap: 18px; }
  .card-back .brand-dot { width: 52px; height: 52px; background: var(--sky); }
  .card-back .brand-name { color: var(--ink); font-size: 42px; }

  .divider {
    position: absolute; left: 300px; right: 56px; top: 250px;
    height: 2px; background: var(--navy);
  }
  .address {
    position: absolute; right: 56px; top: 266px;
    text-align: right; color: var(--text); font-size: 19px; line-height: 1.3;
  }
  .person { position: absolute; left: 60px; top: 232px; }
  .person-name { color: var(--ink); font-size: 34px; font-weight: 800; }
  .person-title { color: var(--text); font-size: 19px; margin-top: 2px; }

  .contacts { position: absolute; left: 60px; top: 330px; list-style: none; }
  .contacts li {
    display: flex; align-items: center; gap: 14px;
    color: var(--text); font-size: 21px; line-height: 1.65;
  }
  .contacts svg { width: 18px; height: 18px; fill: var(--sky); flex: none; }

  .stripe { position: absolute; left: 0; right: 0; bottom: 0; height: 12px; display: flex; }
  .stripe span { flex: 1; }
  .stripe .s-sky { background: var(--sky); }
  .stripe .s-navy { background: var(--navy-deep); }
  .stripe .s-amber { background: var(--amber); }
</style>
</head>
<body>
<main class="sheet">
  <section class="card card-front">
    <div class="brand">
      <span class="brand-dot"></span>
      <span class="brand-name">CrewWell Clinics</span>
    </div>
  </section>

  <section class="card card-back">
    <div class="brand">
      <span class="brand-dot"></span>
      <span class="brand-name">CrewWell Clinics</span>
    </div>

    <div class="person">
      <p class="person-name">Daniel Reyes</p>
      <p class="person-title">CEO &amp; Founder</p>
    </div>

    <div class="divider"></div>

    <p class="address">410 Harbor View Rd, #112<br>Lakemont, OH 43000</p>

    <ul class="contacts">
      <li>
        <svg viewBox="0 0 24 24" aria-hidden="true"><path d="M6.6 10.8a15.1 15.1 0 0 0 6.6 6.6l2.2-2.2a1 1 0 0 1 1-.25 11.4 11.4 0 0 0 3.6.57 1 1 0 0 1 1 1V20a1 1 0 0 1-1 1A17 17 0 0 1 3 4a1 1 0 0 1 1-1h3.5a1 1 0 0 1 1 1c0 1.25.2 2.45.57 3.57a1 1 0 0 1-.25 1z"/></svg>
        877-555-0148
      </li>
      <li>
        <svg viewBox="0 0 24 24" aria-hidden="true"><path d="M3 5h18a1 1 0 0 1 1 1v12a1 1 0 0 1-1 1H3a1 1 0 0 1-1-1V6a1 1 0 0 1 1-1zm9 7.2L20 7H4z"/></svg>
        info@crewwellclinics.com
      </li>
      <li>
        <svg viewBox="0 0 24 24" aria-hidden="true"><path d="M12 2a10 10 0 1 0 0 20 10 10 0 0 0 0-20zm6.9 6h-2.9a15.6 15.6 0 0 0-1.4-3.6A8 8 0 0 1 18.9 8zM12 4c.8 1.2 1.5 2.5 1.9 4h-3.8c.4-1.5 1.1-2.8 1.9-4zM4.3 14a8 8 0 0 1 0-4h3.4a16 16 0 0 0 0 4zm.8 2h2.9c.3 1.3.8 2.5 1.4 3.6A8 8 0 0 1 5.1 16zM8 8H5.1a8 8 0 0 1 4.3-3.6C8.8 5.5 8.3 6.7 8 8zm4 12c-.8-1.2-1.5-2.5-1.9-4h3.8c-.4 1.5-1.1 2.8-1.9 4zm2.3-6H9.7a14.6 14.6 0 0 1 0-4h4.6a14.6 14.6 0 0 1 0 4zm.3 5.6c.6-1.1 1.1-2.3 1.4-3.6h2.9a8 8 0 0 1-4.3 3.6zM16.3 14a16 16 0 0 0 0-4h3.4a8 8 0 0 1 0 4z"/></svg>
        www.crewwellclinics.com
      </li>
    </ul>

    <div class="stripe">
      <span class="s-sky"></span>
      <span class="s-navy"></span>
      <span class="s-amber"></span>
    </div>
  </section>
</main>
</body>
</html>
```